Halverstone Minerals Web Design

Require a Web page design for an international mining and private investment company currently based in Dubai, UAE. I would like to view designs that incorporate our current corporate logo design aimed at communicating global business development/expansion across a diversity of commodities within the mining and investment sectors.

We are a global organisation with global experience and strategy with specific business development focus in Africa, Central and South America.

Target Market(s)

Mining industry, finance, fund raising, brokering, private equity and public stock exchanges.

Industry/Entity Type

Mining

Number of Pages Required

5+ page

Font styles to use
Sans Serif

Colors

Designer to choose colors to be used in the design.

Requirements
Must have
• Corporate logo, description of who we are, what we do, corporate mission, vision & strategy.
Nice to have
• Inclusion of images, photos, interactive maps/graphics and video.

```html
<!DOCTYPE html>
<html lang="en">
<head>
<meta charset="utf-8">
<title>Halverstone Minerals</title>
<link href="https://fonts.googleapis.com/css2?family=Mulish:wght@400;600;700;800&display=swap" rel="stylesheet">
<style>
:root{
  --gold:#cfa234;
  --gold-soft:#c6a95e;
  --ink:#1d1d1d;
  --navy:#1b2431;
  --grey-band:#e6e6e6;
  --muted:#a9a9a9;
  --body:#555;
  --footer:#2a2a2a;
  --white:#fff;
}
*{margin:0;padding:0;box-sizing:border-box}
html,body{width:674px;height:1200px;overflow:hidden;background:var(--white)}
body{font-family:"Mulish",Arial,sans-serif;color:var(--ink);position:relative}
.abs{position:absolute}

/* header */
.brand{left:0;top:0;width:202px;height:48px;background:var(--navy);
  clip-path:polygon(0 0,100% 0,100% 75%,94% 100%,0 100%);z-index:3;
  display:flex;align-items:center;padding-left:75px;gap:6px}
.brand-mark{width:10px;height:10px;background:var(--gold)}
.brand-name{color:var(--gold);font-weight:700;font-size:9.5px;letter-spacing:.4px;text-transform:uppercase;line-height:1.1}
.main-nav{left:202px;top:0;width:472px;height:23px;background:var(--gold-soft);z-index:3;
  display:flex;align-items:center;padding-left:14px;gap:18px}
.main-nav a{font-size:7.2px;color:#3a3220;text-decoration:none;text-transform:uppercase;font-weight:600}
.main-nav a.active{color:#111;font-weight:800}

/* hero */
.hero{left:0;top:0;width:674px;height:346px;
  clip-path:polygon(0 0,100% 0,100% 100%,75px 100%,0 262px)}
.hero-photo{width:100%;height:100%;
  background:linear-gradient(180deg,#4f8fd4 0%,#8fb9e4 45%,#d59d52 70%,#8a4a22 100%)}
.hero-title{left:74px;top:139px;font-size:14px;font-weight:800;line-height:18px;color:#2a2a2a;text-transform:uppercase}
.btn-gold{left:74px;top:178px;width:51px;height:20px;background:var(--gold-soft);
  font-size:6.6px;display:flex;align-items:center;justify-content:center;color:#2a2410;text-transform:uppercase}
.slide-arrow{top:172px;width:16px;height:15px;background:#1b1b1b;display:flex;align-items:center;justify-content:center}

/* sections */
.section-title{left:0;width:674px;text-align:center;color:var(--gold);font-weight:800;font-size:22px}
.title-rule{left:282px;width:110px;height:2px;background:var(--gold)}
.lead{left:74px;width:526px;text-align:center;font-size:10.4px;line-height:15.5px;font-weight:600;color:#1e1e1e}
.copy{left:74px;width:526px;text-align:center;font-size:6.5px;line-height:12.6px;color:var(--body)}

.band{left:0;top:561px;width:674px;height:359px;
  background:linear-gradient(180deg,var(--grey-band) 0%,var(--grey-band) 80%,#d6d6d6 88%,var(--grey-band) 100%);
  clip-path:polygon(0 0,600px 0,100% 75px,100% 100%,0 100%)}
.card{top:663px;width:252px;height:211px}
.card-photo{width:100%;height:130px}
.card-body{height:81px;background:var(--white);padding:10px 12px 0}
.card-title{font-size:12px;font-weight:700;margin-bottom:6px}
.card-text{font-size:6.4px;line-height:12.6px;color:var(--body)}
.card-text span{color:var(--gold)}

.tabs{left:0;top:966px;width:674px;text-align:center;font-size:13.5px;font-weight:800;color:var(--muted)}
.tabs .on{color:var(--gold)}
.tabs .sep{margin:0 9px;font-weight:400}
.btn-outline{left:311px;top:1058px;width:52px;height:21px;border:1px solid #ccc;font-size:6.5px;color:#888;
  display:flex;align-items:center;justify-content:center}

/* footer */
.site-footer{left:0;top:1124px;width:674px;height:76px;background:var(--footer);
  clip-path:polygon(75px 0,100% 0,100% 100%,0 100%,0 75px)}
.foot-links{left:74px;top:1148px;font-size:6.6px;color:#cfcfcf}
.foot-links i{font-style:normal;margin:0 6px}
.foot-copy{left:74px;top:1166px;font-size:6.6px;color:#bdbdbd}
.foot-contact{right:119px;text-align:right;font-size:6.6px;color:#cfcfcf}
.social{top:1154px;width:14px;height:14px;border-radius:50%;background:#5a5a5a}
</style>
</head>
<body>

<header>
  <div class="abs brand"><span class="brand-mark"></span><span class="brand-name">Halverstone<br>Minerals</span></div>
  <nav class="abs main-nav">
    <a class="active" href="#">Home</a><a href="#">Who we are</a><a href="#">What we do</a>
    <a href="#">Corporate mission</a><a href="#">Vision &amp; strategy</a><a href="#">Contact us</a>
  </nav>
</header>

<section class="abs hero">
  <div class="hero-photo" role="img" aria-label="Yellow excavator bucket tipping red earth against a blue sky"></div>
</section>
<h1 class="abs hero-title">International mining and<br>private investment company</h1>
<div class="abs btn-gold">Read more</div>
<div class="abs slide-arrow" style="left:0">
  <svg width="9" height="8" viewBox="0 0 9 8"><path d="M8 4H1M4 1L1 4l3 3" stroke="#fff" stroke-width="1.4" fill="none"/></svg>
</div>
<div class="abs slide-arrow" style="right:0">
  <svg width="9" height="8" viewBox="0 0 9 8"><path d="M1 4h7M5 1l3 3-3 3" stroke="#fff" stroke-width="1.4" fill="none"/></svg>
</div>

<section>
  <h2 class="abs section-title" style="top:384px">WHO WE ARE</h2>
  <div class="abs title-rule" style="top:420px"></div>
  <p class="abs lead" style="top:434px">We are a global organisation with global experience and strategy with specific business development focus in Africa, Central and South America.</p>
  <p class="abs copy" style="top:467px">Vestibulum condimentum, risus ut posuere cursus, velit justo accumsan sem, lobortis aliquet metus dui eu libero. Pellentesque a imperdiet dolor, et auctor est. Fusce sollicitudin lorem et luctus volutpat. Proin placerat dapibus gravida. In tristique tristique nulla eget hendrerit. Maecenas vel tortor accumsan quam varius imperdiet vel eget elit. Aenean facilisis tincidunt lectus, id dictum nisi luctus eget. Vivamus efficitur ex condimentum, malesuada eros eget, feugiat nibh. Sed tellus ex, imperdiet eget gravida sit amet, volutpat eget turpis. In nec ultricies est. Etiam mattis augue vehicula odio posuere, sit amet tempus lectus luctus.</p>
</section>

<section>
  <div class="abs band"></div>
  <h2 class="abs section-title" style="top:599px">WHAT WE DO</h2>
  <div class="abs title-rule" style="top:636px"></div>

  <article class="abs card" style="left:74px">
    <div class="card-photo" role="img" aria-label="Hand holding a lump of coal at a mine site"
      style="background:linear-gradient(135deg,#6b5a4a,#3a3330 55%,#8a7a68);clip-path:polygon(16px 0,100% 0,100% 100%,0 100%,0 16px)"></div>
    <div class="card-body" style="clip-path:polygon(0 0,100% 0,100% 56%,calc(100% - 24px) 100%,0 100%)">
      <h3 class="card-title">Mining</h3>
      <p class="card-text">Maecenas vel tortor accumsan quam varius imperdiet vel eget elit. Aenean facilisis tincidunt lectus, id dictum nisi luctus eget. Vivamus efficitur ex condimentum, malesuada eros eget, feugiat nibh. <span>Read More</span></p>
    </div>
  </article>

  <article class="abs card" style="left:348px">
    <div class="card-photo" role="img" aria-label="Hand stacking coins beside a rising growth chart"
      style="background:linear-gradient(135deg,#1e2f4a,#3c5a80 55%,#7fa6c9);clip-path:polygon(0 0,calc(100% - 24px) 0,100% 24px,100% 100%,0 100%)"></div>
    <div class="card-body" style="clip-path:polygon(0 0,100% 0,100% 100%,24px 100%,0 56%);padding-left:21px">
      <h3 class="card-title">Investment</h3>
      <p class="card-text">Maecenas vel tortor accumsan quam varius imperdiet vel eget elit. Aenean facilisis tincidunt lectus, id dictum nisi luctus eget. Vivamus efficitur ex condimentum, malesuada eros eget, feugiat nibh. <span>Read More</span></p>
    </div>
  </article>
</section>

<section>
  <div class="abs tabs"><span class="on">CORPORATE MISSION</span><span class="sep">/</span>VISION<span class="sep">/</span>STRATEGY</div>
  <div class="abs" style="left:178px;top:997px;width:318px;height:1px;background:#ccc"></div>
  <div class="abs" style="left:178px;top:996px;width:142px;height:3px;background:var(--gold)"></div>
  <p class="abs lead" style="top:1013px;font-weight:600">Vivamus eleifend vitae nulla vel malesuada. In ac malesuada lacus, et consectetur ante. Fusce vitae lectus sit amet mi pulvinar maximus. Aenean placerat, nibh vel accumsan aliquet.</p>
  <div class="abs btn-outline">Read More</div>
</section>

<footer>
  <div class="abs site-footer"></div>
  <div class="abs foot-links">Home<i>|</i>Who we are<i>|</i>What we do<i>|</i>Corporate mission<i>|</i>Vision &amp; strategy<i>|</i>Contact us</div>
  <div class="abs foot-copy">Copyright © 2018 Halverstone Minerals. &nbsp;All rights reserved.</div>
  <div class="abs foot-contact" style="top:1148px">Call : 555 014 2087</div>
  <div class="abs foot-contact" style="top:1166px">Email : info@halverstoneminerals.com</div>
  <div class="abs social" style="left:567px"></div>
  <div class="abs social" style="left:585px"></div>
</footer>

</body>
</html>
```